Business Card Design Project - 2 sided

We need a business card design for a card having one business on each side (ie. two businesses on one card). Would like a design that incorporates logo, tagline and normal fields (name, position, address, phone).

Would also like an allowance for small font text along the bottom (text to be determined, but less than 50 characters).

NB. Attached logo for Harbor Quill has two variations - either can be used.

www.harborquill-example.com / www.velmaro-example.com

```html
<!DOCTYPE html>
<html lang="en">
<head>
<meta charset="utf-8">
<title>Harbor Quill / Velmaro business card</title>
<link rel="stylesheet" href="https://fonts.googleapis.com/css2?family=Open+Sans:wght@400;600;700&display=swap">
<style>
  :root {
    --backdrop: #e9e7e4;
    --card: #ffffff;
    --text: #4a4a4a;
    --green: #8dc63f;
    --navy: #2b2a6b;
    --blue: #1e7bb2;
    --divider: #b9b9b9;
  }
  * { box-sizing: border-box; margin: 0; padding: 0; }
  html, body { width: 1200px; height: 402px; overflow: hidden; }
  body {
    background: var(--backdrop);
    font-family: "Open Sans", Arial, sans-serif;
    color: var(--text);
    position: relative;
  }
  .card {
    position: absolute;
    top: 56px;
    width: 512px;
    height: 290px;
    background: var(--card);
    box-shadow: 0 1px 4px rgba(0,0,0,.18);
    overflow: hidden;
  }
  .card--harbor { left: 62px; --accent: var(--navy); }
  .card--velmaro { left: 626px; --accent: var(--blue); }

  .brand {
    position: absolute;
    left: 0; right: 0;
    text-align: center;
  }
  .brand__name {
    display: inline-flex;
    align-items: center;
    gap: 10px;
    font-weight: 600;
    color: var(--accent);
    line-height: 1;
  }
  .brand__dot {
    display: inline-block;
    border-radius: 50%;
    background: var(--green);
  }
  .card--harbor .brand { top: 80px; }
  .card--harbor .brand__name { font-size: 24px; letter-spacing: 1.5px; }
  .card--harbor .brand__dot { width: 14px; height: 14px; }
  .card--harbor .brand__tagline {
    font-size: 8.5px; font-weight: 600; color: #333; margin-top: 4px;
  }
  .card--velmaro .brand { top: 58px; }
  .card--velmaro .brand__name { font-size: 42px; letter-spacing: .5px; }
  .card--velmaro .brand__dot { width: 34px; height: 34px; }
  .card--velmaro .brand__tagline {
    font-size: 13px; color: #333; letter-spacing: .6px; margin-top: 4px; padding-left: 50px;
  }

  .address {
    position: absolute;
    right: 272px;
    top: 144px;
    text-align: right;
    font-size: 12.5px;
    line-height: 17.5px;
  }
  .address__gap { height: 19px; }
  .divider {
    position: absolute;
    left: 262px;
    top: 146px;
    width: 1px;
    height: 82px;
    background: linear-gradient(var(--card), var(--divider) 25%, var(--divider) 75%, var(--card));
  }
  .contacts {
    position: absolute;
    left: 277px;
    top: 144px;
    list-style: none;
    font-size: 12.5px;
    line-height: 17.5px;
  }
  .contacts li { display: flex; align-items: center; gap: 5px; }
  .contacts svg { width: 10px; height: 10px; flex: none; }

  .bands { position: absolute; left: 0; bottom: 0; }
  .holder {
    position: absolute;
    left: 294px;
    top: 262px;
    color: #fff;
    font-size: 16px;
    font-weight: 700;
    white-space: nowrap;
  }
  .holder__title { font-weight: 400; font-size: 12.5px; }
</style>
</head>
<body>

<svg width="0" height="0" style="position:absolute">
  <defs>
    <symbol id="icon-phone" viewBox="0 0 10 10">
      <circle cx="5" cy="5" r="5" fill="#8dc63f"/>
      <path d="M3 2.6c.4-.3.7-.2.9.2l.4.8c.1.3 0 .5-.2.6l-.3.2c.3.7.8 1.2 1.5 1.5l.2-.3c.1-.2.4-.3.6-.2l.8.4c.4.2.5.5.2.9-.5.6-1.2.7-2 .3C4 6.4 3.6 6 3.1 5 2.7 4 2.6 3.1 3 2.6z" fill="#fff"/>
    </symbol>
    <symbol id="icon-mobile" viewBox="0 0 10 10">
      <rect x="2.8" y="0.5" width="4.4" height="9" rx="1" fill="#8dc63f"/>
      <rect x="3.6" y="1.6" width="2.8" height="5.2" fill="#fff"/>
    </symbol>
    <symbol id="icon-fax" viewBox="0 0 10 10">
      <rect x="0.5" y="3.5" width="9" height="5.5" rx="1" fill="#8dc63f"/>
      <rect x="2.5" y="1" width="5" height="3" fill="#8dc63f"/>
      <rect x="2.5" y="5" width="5" height="1.2" fill="#fff"/>
    </symbol>
    <symbol id="icon-mail" viewBox="0 0 10 10">
      <rect x="0.5" y="2" width="9" height="6.5" rx="1" fill="#8dc63f"/>
      <path d="M1.2 2.8 5 5.6l3.8-2.8" fill="none" stroke="#fff" stroke-width="0.9"/>
    </symbol>
    <symbol id="icon-web" viewBox="0 0 10 10">
      <circle cx="5" cy="5" r="4.6" fill="#8dc63f"/>
      <path d="M.6 5h8.8M5 .5c-2 2.5-2 6.5 0 9M5 .5c2 2.5 2 6.5 0 9" fill="none" stroke="#fff" stroke-width="0.7"/>
    </symbol>
  </defs>
</svg>

<section class="card card--harbor">
  <div class="brand">
    <div class="brand__name"><span class="brand__dot"></span>HARBOR QUILL</div>
    <p class="brand__tagline">Website Translation and Localisation Specialist...</p>
  </div>
  <div class="address">
    <p>xxxxxxxxxxxxxxxxxxxxx</p>
    <p>xxxxxxxxxxxxxxxxxxxxx</p>
    <div class="address__gap"></div>
    <p>Complex name, Street</p>
    <p>City, State, zip code</p>
  </div>
  <div class="divider"></div>
  <ul class="contacts">
    <li><svg><use href="#icon-phone"/></svg>123-456-7890</li>
    <li><svg><use href="#icon-mobile"/></svg>123-456-7890</li>
    <li><svg><use href="#icon-fax"/></svg>123-456-7890</li>
    <li><svg><use href="#icon-mail"/></svg>name@website.com</li>
    <li><svg><use href="#icon-web"/></svg>www.website.com</li>
  </ul>
  <svg class="bands" width="512" height="48" viewBox="0 0 512 48">
    <polygon points="0,23 206,23 198,48 0,48" fill="var(--green)"/>
    <polygon points="228,0 512,0 512,48 207,48" fill="var(--navy)"/>
  </svg>
  <p class="holder">Your Name <span class="holder__title">/ Title</span></p>
</section>

<section class="card card--velmaro">
  <div class="brand">
    <div class="brand__name"><span class="brand__dot"></span>velmaro</div>
    <p class="brand__tagline">Professional SEO Services</p>
  </div>
  <div class="address">
    <p>xxxxxxxxxxxxxxxxxxxxx</p>
    <p>xxxxxxxxxxxxxxxxxxxxx</p>
    <div class="address__gap"></div>
    <p>Complex name, Street</p>
    <p>City, State, zip code</p>
  </div>
  <div class="divider"></div>
  <ul class="contacts">
    <li><svg><use href="#icon-phone"/></svg>123-456-7890</li>
    <li><svg><use href="#icon-mobile"/></svg>123-456-7890</li>
    <li><svg><use href="#icon-fax"/></svg>123-456-7890</li>
    <li><svg><use href="#icon-mail"/></svg>name@website.com</li>
    <li><svg><use href="#icon-web"/></svg>www.website.com</li>
  </ul>
  <svg class="bands" width="512" height="48" viewBox="0 0 512 48">
    <polygon points="0,23 218,23 208,48 0,48" fill="var(--green)"/>
    <polygon points="243,0 512,0 512,48 217,48" fill="var(--blue)"/>
  </svg>
  <p class="holder">Your Name <span class="holder__title">/ Title</span></p>
</section>

</body>
</html>
```